Brevlon Website Design - Wordpress

Need a website WordPress design for our existing website that we just stood up. The logo is already in place and name. Brevlon.example We are a company which makes connections with our clients through educating them and providing networking events. We would like for the website to show a VIP/special feel to it.

Target Market(s)

Business executives and employees. Age group 26-65 in the following sectors:
- Technology
- Human Resources
- Finance
- Sales

Industry/Entity Type

Technical Service

Number of Pages Required

4 page

Font styles to use
Sans Serif

Requirements
Must have
• Must be something for Wordpress
Nice to have
• Would like this to be professional but look cutting edge and VIP.

```html
<!DOCTYPE html>
<html lang="en">
<head>
<meta charset="utf-8">
<title>Brevlon Connect</title>
<link rel="stylesheet" href="https://fonts.googleapis.com/css2?family=Titillium+Web:wght@400;600;700&family=Open+Sans:wght@400;600;700&display=swap">
<style>
:root{
  --blue:#1c4f8f;
  --blue-bright:#2160b0;
  --red:#c8202b;
  --purple:#6b2a8c;
  --green:#3b9a3c;
  --yellow:#e2a414;
  --ink:#222;
  --text:#555;
  --light:#eceded;
  --dark:#141414;
  --white:#fff;
}
*{box-sizing:border-box;margin:0;padding:0}
html,body{width:1200px;height:4358px;overflow:hidden}
body{position:relative;font-family:"Open Sans",sans-serif;color:var(--text);background:var(--white)}
.abs{position:absolute}
h1,h2,h3,h4{font-family:"Titillium Web",sans-serif}

/* hero */
.hero{left:0;top:0;width:1200px;height:712px;background:linear-gradient(180deg,#3a3a3a 0%,#9a9a9a 45%,#cfcfcf 100%);overflow:hidden}
.hero-visual{left:50px;top:170px;width:520px;height:480px;border-radius:50% 45% 40% 48%;background:radial-gradient(circle at 55% 45%,#d8d8d8 0%,#7b7b7b 45%,#2c2c2c 100%);opacity:.9}
.brand{left:150px;top:42px;display:flex;align-items:center;gap:14px;color:var(--white);font-family:"Titillium Web",sans-serif;font-size:44px;font-weight:400;letter-spacing:4px}
.brand-dot{width:40px;height:40px;background:var(--blue-bright)}
.call{left:750px;top:42px;color:var(--white);font-size:22px;display:flex;align-items:center;gap:12px}
.call b{font-weight:700}
.nav{left:592px;top:108px;display:flex;gap:22px;font-family:"Titillium Web",sans-serif;font-weight:700;font-size:17px;color:var(--white)}
.hero-title{left:693px;top:262px;color:var(--white);font-size:56px;line-height:68px;font-weight:700;letter-spacing:1px}
.btn-solid{left:700px;top:423px;width:186px;height:48px;background:var(--blue);color:var(--white);font-weight:700;font-size:16px;display:flex;align-items:center;justify-content:center;border:1px solid #6a8fc4}
.dots{left:697px;top:507px;display:flex;gap:12px}
.dots span{width:17px;height:17px;border-radius:50%;border:2px solid var(--white)}
.dots span:first-child{background:var(--white)}

/* welcome */
.welcome-title{left:145px;top:850px;font-size:41px;line-height:48px;font-weight:700;color:var(--ink)}
.welcome-title span{color:var(--blue-bright)}
.welcome-text{left:145px;top:962px;width:450px;font-size:15px;line-height:32px}
.btn-outline{left:145px;top:1187px;width:152px;height:46px;border:2px solid var(--blue);color:var(--blue);font-weight:700;font-size:14px;display:flex;align-items:center;justify-content:center}
.welcome-visual{left:635px;top:845px;width:395px;height:470px;background:linear-gradient(180deg,#9aa6b0 0%,#4b545c 55%,#23272b 100%)}

/* offer */
.offer{left:0;top:1355px;width:1200px;height:790px;background:linear-gradient(180deg,#2e2e30 0%,#1c1d22 55%,#333 100%);overflow:hidden}
.section-title{width:1200px;text-align:center;font-size:37px;font-weight:400;color:var(--ink)}
.section-title b{font-weight:700}
.rule{width:96px;height:3px;left:552px}
.offer-card{top:1665px;width:223px;height:340px;color:var(--white);text-align:center;clip-path:polygon(0 0,100% 0,100% 88%,50% 100%,0 88%);padding-top:30px}
.offer-card .icon{width:90px;height:90px;border-radius:50%;background:var(--white);margin:0 auto 16px;display:flex;align-items:center;justify-content:center}
.offer-card h3{font-size:19px;font-weight:700;margin-bottom:8px}
.offer-card p{font-size:12px;line-height:22px;padding:0 12px;height:66px;overflow:hidden}
.offer-card .chev{margin-top:22px;display:flex;justify-content:center}

/* strategy */
.strategy{left:0;top:2145px;width:1200px;height:860px;background:var(--light);overflow:hidden}
.strategy-intro{left:330px;top:2328px;width:540px;text-align:center;font-size:14px;line-height:28px}
.point{width:285px;font-size:14px;line-height:28px}
.point h4{font-size:21px;font-weight:700;color:var(--ink);margin-bottom:6px}
.point.left{text-align:right;left:60px}
.point.right{left:855px}
.point-icon{width:92px;height:92px;border-radius:50%;display:flex;align-items:center;justify-content:center;border:4px solid var(--white)}
.strategy-visual{left:440px;top:2460px;width:320px;height:340px;background:linear-gradient(135deg,#2a5a96 0%,#9b2a4a 50%,#c7941c 100%);opacity:.85;border-radius:16px}

/* news */
.news-card{top:3195px;width:293px;height:375px;background:var(--white);box-shadow:0 2px 10px rgba(0,0,0,.15);text-align:center}
.news-img{height:190px}
.news-card h4{font-family:"Open Sans",sans-serif;font-size:17px;font-weight:400;color:var(--blue);line-height:24px;margin:18px 30px 6px}
.news-date{font-size:14px;color:var(--blue);margin-bottom:10px}
.news-card p{font-size:12px;line-height:20px;padding:0 36px}

/* footer */
.footer{left:0;top:3680px;width:1200px;height:678px;background:var(--dark);color:var(--white);overflow:hidden}
.foot-title{top:3818px;font-size:21px;font-weight:700;color:var(--white)}
.foot-rule{top:3872px;width:56px;height:2px;background:var(--white)}
.field{left:145px;width:362px;height:33px;border:1px solid #777;font-size:12px;padding:8px 10px;color:#ddd}
.submit{left:145px;top:4135px;width:178px;height:32px;background:var(--red);color:var(--white);font-weight:700;font-size:13px;display:flex;align-items:center;justify-content:center}
.contact-row{left:568px;display:flex;gap:22px;font-size:14px;line-height:22px;color:var(--white)}
.contact-row .ico{width:30px;height:30px;border-radius:50%;border:1px solid #aaa;flex:none;display:flex;align-items:center;justify-content:center}
.socials{left:570px;top:4125px;display:flex;gap:10px}
.socials span{width:30px;height:30px;border-radius:50%;border:2px solid var(--white)}
.links{left:900px;top:3912px;font-size:14px;line-height:32px;list-style:none;color:var(--white)}
.copyright{left:0;top:4280px;width:1200px;text-align:center;font-size:14px;color:var(--white)}
</style>
</head>
<body>

<!-- hero -->
<section class="abs hero">
  <div class="abs hero-visual" role="img" aria-label="Photo of a head silhouette formed from clocks with a wind-up key"></div>
  <svg class="abs" style="left:0;top:640px" width="1200" height="72" viewBox="0 0 1200 72"><polygon points="0,22 700,72 0,72" fill="#1c4f8f"/><polygon points="0,40 1200,72 0,72" fill="#fff"/></svg>
</section>
<div class="abs brand"><span class="brand-dot"></span>BREVLON</div>
<div class="abs call">
  <svg width="32" height="32" viewBox="0 0 32 32"><circle cx="16" cy="16" r="14.5" fill="none" stroke="#fff" stroke-width="2"/><path d="M11 9l3 0 1 4-2 1.5c1 2 2.5 3.5 4.5 4.5L19 17l4 1v3c-7 1-13-5-12-12z" fill="#fff"/></svg>
  <span>Call Us : <b>1-855-555-0142</b></span>
</div>
<nav class="abs nav"><span>HOME</span><span>EVENTS</span><span>EXPAND</span><span>X</span><span>ABOUT</span><span>CONNECT</span></nav>
<h1 class="abs hero-title">EXPAND YOUR<br>BUSINESS</h1>
<div class="abs btn-solid">LEARN MORE</div>
<div class="abs dots"><span></span><span></span><span></span></div>

<!-- welcome -->
<h2 class="abs welcome-title">Welcome to<br><span>Brevlon Connect</span></h2>
<p class="abs welcome-text">Sed ut perspiciatis unde omnis iste natus error sit voluptatem accusantium doloremque laudantium, totam rem aperiam, eaque ipsa quae ab illo inventore veritatis et quasi architecto beatae vitae dicta sunt explicabo. Nemo enim ipsam vptatem quia voluptas sit aspernatur aut odit aut fugit, sed quia consequuntur magni dolores eos</p>
<div class="abs btn-outline">READ MORE</div>
<div class="abs welcome-visual" role="img" aria-label="Photo of a person standing in a bright doorway"></div>

<!-- offer -->
<section class="abs offer" role="img" aria-label="Dim photo of an office desk with a city view">
  <svg class="abs" style="left:0;top:0" width="1200" height="60" viewBox="0 0 1200 60"><polygon points="0,0 1200,0 1200,30 0,0" fill="#eceded"/><polygon points="880,0 1200,0 1200,60" fill="#e2a414"/><polygon points="0,0 1200,0 1200,12 0,0" fill="#fff"/></svg>
</section>
<h2 class="abs section-title" style="left:0;top:1497px;color:#fff"><b>WHAT WE</b> OFFER YOU</h2>
<div class="abs rule" style="top:1585px;background:#fff"></div>

<div class="abs offer-card" style="left:142px;background:var(--blue)">
  <div class="icon"><svg width="48" height="48" viewBox="0 0 48 48" fill="none" stroke="#1c4f8f" stroke-width="2.5"><rect x="14" y="8" width="28" height="20"/><circle cx="10" cy="20" r="4"/><path d="M4 40v-10h12v10M19 15h18M19 21h12"/></svg></div>
  <h3>EDUCATE</h3>
  <p>At BREVLON, we provide effective training and learning as the foundation for building a healthy, successful company.</p>
  <div class="chev"><svg width="16" height="14" viewBox="0 0 16 14" fill="none" stroke="#fff" stroke-width="2"><path d="M3 2l5 4 5-4M3 8l5 4 5-4"/></svg></div>
</div>
<div class="abs offer-card" style="left:377px;background:var(--red)">
  <div class="icon"><svg width="48" height="48" viewBox="0 0 48 48" fill="none" stroke="#c8202b" stroke-width="2.5"><circle cx="24" cy="24" r="16"/><circle cx="24" cy="24" r="6"/><path d="M24 4v6M24 38v6M4 24h6M38 24h6"/></svg></div>
  <h3>EQUIP</h3>
  <p>Through our connected ecosystem of companies, we'll help find the right partners for equipping you to move forward.</p>
  <div class="chev"><svg width="16" height="14" viewBox="0 0 16 14" fill="none" stroke="#fff" stroke-width="2"><path d="M3 2l5 4 5-4M3 8l5 4 5-4"/></svg></div>
</div>
<div class="abs offer-card" style="left:612px;background:var(--purple)">
  <div class="icon"><svg width="48" height="48" viewBox="0 0 48 48" fill="none" stroke="#6b2a8c" stroke-width="2.5"><path d="M10 20a15 15 0 0 1 27-6M38 28a15 15 0 0 1-27 6"/><path d="M37 6v8h-8M11 42v-8h8"/></svg></div>
  <h3>EXCHANGE</h3>
  <p>We connect you with others who have successfully implemented our X Strategy to facilitate growth in their</p>
  <div class="chev"><svg width="16" height="14" viewBox="0 0 16 14" fill="none" stroke="#fff" stroke-width="2"><path d="M3 2l5 4 5-4M3 8l5 4 5-4"/></svg></div>
</div>
<div class="abs offer-card" style="left:847px;background:var(--green)">
  <div class="icon"><svg width="48" height="48" viewBox="0 0 48 48" fill="none" stroke="#3b9a3c" stroke-width="2.5"><circle cx="24" cy="20" r="14"/><circle cx="24" cy="20" r="8"/><circle cx="24" cy="20" r="2"/><path d="M18 34l-4 10M30 34l4 10"/></svg></div>
  <h3>EXPAND</h3>
  <p>Our goal is to help you and your business increase productivity and scale through effective strategy and healthy culture.</p>
  <div class="chev"><svg width="16" height="14" viewBox="0 0 16 14" fill="none" stroke="#fff" stroke-width="2"><path d="M3 2l5 4 5-4M3 8l5 4 5-4"/></svg></div>
</div>

<!-- strategy -->
<section class="abs strategy">
  <svg class="abs" style="left:0;top:735px" width="1200" height="125" viewBox="0 0 1200 125"><polygon points="0,45 660,125 0,125" fill="#6b2a8c"/><polygon points="600,110 1200,60 1200,125 560,125" fill="#e2a414"/><polygon points="0,80 1200,125 0,125" fill="#fff"/></svg>
</section>
<h2 class="abs section-title" style="left:0;top:2222px">IT'S ABOUT <b>OUR UNIQUE X STRATEGY</b></h2>
<div class="abs rule" style="top:2300px;background:#333"></div>
<p class="abs strategy-intro">BREVLON provides impactful connection opportunities to help educate, equip and expand you and your business</p>

<div class="abs strategy-visual" role="img" aria-label="Four-part strategy graphic in blue, red, purple and gold"></div>

<div class="abs point left" style="top:2450px"><h4>Mind Thought</h4>Sed ut perspiciatis unde omnis iste natus error sit voluptatem accusantium doloremque laudantium, totam rem aperiam, eaque ipsa quae</div>
<div class="abs point right" style="top:2450px"><h4>Heart Emotions</h4>Sed ut perspiciatis unde omnis iste natus error sit voluptatem accusantium doloremque laudantium, totam rem aperiam, eaque ipsa quae</div>
<div class="abs point left" style="top:2665px"><h4>Soul Intuition</h4>Sed ut perspiciatis unde omnis iste natus error sit voluptatem accusantium doloremque laudantium, totam rem aperiam, eaque ipsa quae</div>
<div class="abs point right" style="top:2665px"><h4>Strength Energy</h4>Sed ut perspiciatis unde omnis iste natus error sit voluptatem accusantium doloremque laudantium, totam rem aperiam, eaque ipsa quae</div>

<div class="abs point-icon" style="left:376px;top:2450px;background:var(--blue)"><svg width="40" height="40" viewBox="0 0 40 40" fill="none" stroke="#fff" stroke-width="2.5"><circle cx="20" cy="20" r="12"/><circle cx="20" cy="20" r="4"/></svg></div>
<div class="abs point-icon" style="left:732px;top:2450px;background:var(--red)"><svg width="40" height="40" viewBox="0 0 40 40"><path d="M20 34L7 20a7 7 0 0 1 13-8 7 7 0 0 1 13 8z" fill="none" stroke="#fff" stroke-width="2.5"/></svg></div>
<div class="abs point-icon" style="left:376px;top:2710px;background:var(--purple)"><svg width="40" height="40" viewBox="0 0 40 40" fill="none" stroke="#fff" stroke-width="2.5"><rect x="10" y="6" width="20" height="14"/><path d="M6 34l6-8 6 8M22 34l6-8 6 8"/></svg></div>
<div class="abs point-icon" style="left:732px;top:2710px;background:var(--yellow)"><svg width="40" height="40" viewBox="0 0 40 40" fill="none" stroke="#fff" stroke-width="2.5"><circle cx="20" cy="20" r="7"/><path d="M20 5v6M20 29v6M5 20h6M29 20h6M9 9l4 4M27 27l4 4M31 9l-4 4M13 27l-4 4"/></svg></div>

<!-- news -->
<h2 class="abs section-title" style="left:0;top:3040px;font-weight:700">LATEST <span style="color:var(--blue-bright)">NEWS</span></h2>
<div class="abs rule" style="top:3130px;width:80px;left:560px;background:var(--blue)"></div>

<article class="abs news-card" style="left:133px">
  <div class="news-img" role="img" aria-label="Illustration of a collage of business ideas" style="background:linear-gradient(160deg,#8fb1c9,#c98e5a)"></div>
  <h4>Sed ut perspiciatis unde omnis iste natus</h4>
  <div class="news-date">&#9638; Oct 01, 2018</div>
  <p>Sed ut perspiciatis unde omnis iste natus error sit voluptatem accusantium dolrque laudantium, totam</p>
</article>
<article class="abs news-card" style="left:455px">
  <div class="news-img" role="img" aria-label="Photo of gears at sunset" style="background:linear-gradient(180deg,#e8b352,#5a3a1a)"></div>
  <h4>Sed ut perspiciatis unde omnis iste natus</h4>
  <div class="news-date">&#9638; Oct 01, 2018</div>
  <p>Sed ut perspiciatis unde omnis iste natus error sit voluptatem accusantium dolrque laudantium, totam</p>
</article>
<article class="abs news-card" style="left:775px">
  <div class="news-img" role="img" aria-label="Photo of a glowing light bulb" style="background:radial-gradient(circle at 50% 40%,#ffd27a,#c3501a 55%,#2a1408)"></div>
  <h4>Sed ut perspiciatis unde omnis iste natus</h4>
  <div class="news-date">&#9638; Oct 01, 2018</div>
  <p>Sed ut perspiciatis unde omnis iste natus error sit voluptatem accusantium dolrque laudantium, totam</p>
</article>

<!-- footer -->
<footer class="abs footer">
  <svg class="abs" style="left:0;top:0" width="1200" height="90" viewBox="0 0 1200 90"><polygon points="0,0 1200,0 1200,90" fill="#c8202b"/><polygon points="0,0 1200,0 1200,55" fill="#fff"/></svg>
</footer>
<h3 class="abs foot-title" style="left:145px">REQUEST A QUOTE</h3>
<div class="abs foot-rule" style="left:145px"></div>
<div class="abs field" style="top:3920px">First Name</div>
<div class="abs field" style="top:3960px">Email Address</div>
<div class="abs field" style="top:4000px">Phone Number</div>
<div class="abs field" style="top:4040px;height:58px">Message</div>
<div class="abs submit">SUBMIT</div>

<h3 class="abs foot-title" style="left:568px">CONTACT US</h3>
<div class="abs foot-rule" style="left:568px"></div>
<div class="abs contact-row" style="top:3915px"><span class="ico"><svg width="14" height="16" viewBox="0 0 14 16"><path d="M7 15S1 9 1 6a6 6 0 0 1 12 0c0 3-6 9-6 9z" fill="#fff"/><circle cx="7" cy="6" r="2" fill="#141414"/></svg></span><span>Address:<br>Av. Lindero Nº 2150<br>Ciudad Norte – Valle Alto</span></div>
<div class="abs contact-row" style="top:3998px"><span class="ico"><svg width="14" height="14" viewBox="0 0 14 14"><path d="M2 1h3l1 3-2 1c1 2 2 3 4 4l1-2 3 1v3C6 12 1 7 2 1z" fill="#fff"/></svg></span><span>Phone:<br><span style="font-size:17px">1-855-555-0142</span></span></div>
<div class="abs contact-row" style="top:4060px"><span class="ico"><svg width="14" height="10" viewBox="0 0 14 10"><rect x=".5" y=".5" width="13" height="9" fill="none" stroke="#fff"/><path d="M1 1l6 5 6-5" fill="none" stroke="#fff"/></svg></span><span>Email:<br>connect@brevlon.example</span></div>
<div class="abs socials" aria-label="Social links"><span></span><span></span><span></span></div>

<h3 class="abs foot-title" style="left:900px">QUICK LINKS</h3>
<div class="abs foot-rule" style="left:900px"></div>
<ul class="abs links"><li>Home</li><li>Events</li><li>Expand</li><li>X</li><li>About</li><li>Connect</li></ul>

<p class="abs copyright">© Copyright 2019 BREVLON. All Rights Reserved.</p>

</body>
</html>
```